Sales Page Header Design Project

Hi,
I need a background image created for this sales page: http://trimventurecamp.com
Width: 977 px
Height: 150 px
Here are a few sample designs to work with: http://firmsummitschool.com/
http://craftingamarkweb.com/wp-content/uploads/2011/02/experts1.png
Must be sharp, professional looking and uncluttered.
Colours: Must include blue (I like the blue on the on the current sales page, but will leave shade and colour combinations to your creativity)
Text = Tobi Wanrenu Presents
Trim Venture Camp
Your Blueprint for Building a Profitable, Sustainable Business in Today's Economy!
Any questions, give me a shout
Entrepreneurs and Business Owners, aged 21 to 45
Business

```html
<!DOCTYPE html>
<html lang="en">
<head>
<meta charset="utf-8">
<title>Trim Venture Camp – Sales Page Header</title>
<link rel="stylesheet" href="https://fonts.googleapis.com/css2?family=Arimo:ital,wght@1,400;1,700&family=Inter:wght@300;800&display=swap">
<style>
  :root {
    --backdrop-light: #ffffff;
    --backdrop-mid: #f1f1f1;
    --backdrop-edge: #bdbdbd;
    --band-top: #004c9e;
    --band-mid: #0078c4;
    --band-bottom: #009fd9;
    --presenter: #b7c3cf;
    --presents: #9fb7cc;
    --title: #ffffff;
    --title-shadow: rgba(0, 20, 50, 0.55);
    --tagline: #ffff33;
    --tagline-shadow: rgba(0, 25, 60, 0.8);
    --icon-dark: #4a4d52;
    --icon-light: #6cc4ec;
  }
  * { margin: 0; padding: 0; box-sizing: border-box; }
  html, body {
    width: 1200px;
    height: 1000px;
    overflow: hidden;
  }
  body {
    position: relative;
    background: radial-gradient(ellipse 75% 70% at 50% 48%, var(--backdrop-light) 0%, var(--backdrop-light) 45%, var(--backdrop-mid) 70%, var(--backdrop-edge) 100%);
  }
  .header-band {
    position: absolute;
    left: 112px;
    top: 425px;
    width: 977px;
    height: 150px;
    background: linear-gradient(180deg, var(--band-top) 0%, var(--band-top) 12%, var(--band-mid) 55%, var(--band-bottom) 100%);
    color: var(--title);
  }
  .presenter {
    position: absolute;
    top: 23px;
    left: 0;
    width: 100%;
    text-align: center;
    font-family: "Inter", Arial, sans-serif;
    font-weight: 300;
    font-size: 15px;
    color: var(--presenter);
    white-space: nowrap;
  }
  .presenter .presents {
    font-size: 9px;
    letter-spacing: 1.2px;
    color: var(--presents);
    margin-left: 3px;
  }
  .title {
    position: absolute;
    top: 52px;
    left: 0;
    width: 100%;
    display: flex;
    justify-content: center;
    align-items: center;
    gap: 8px;
    font-family: "Inter", Arial, sans-serif;
    font-size: 51px;
    line-height: 64px;
    white-space: nowrap;
    text-shadow: 2px 2px 2px var(--title-shadow);
  }
  .title-light { font-weight: 300; letter-spacing: -0.5px; }
  .title-bold { font-weight: 800; letter-spacing: 0.5px; }
  .growth-icon {
    width: 62px;
    height: 64px;
    border-radius: 2px;
    background: linear-gradient(90deg, var(--icon-dark) 0%, var(--icon-dark) 35%, var(--icon-light) 70%, var(--icon-light) 100%);
  }
  .tagline {
    position: absolute;
    top: 114px;
    left: 0;
    width: 100%;
    text-align: center;
    font-family: "Arimo", Arial, sans-serif;
    font-style: italic;
    font-size: 15.5px;
    letter-spacing: 0.2px;
    color: var(--tagline);
    text-shadow: 1px 1px 1px var(--tagline-shadow), 0 0 2px var(--tagline-shadow);
    white-space: nowrap;
  }
</style>
</head>
<body>
  <header class="header-band">
    <p class="presenter">Tobi Wanrenu <span class="presents">Presents</span></p>
    <h1 class="title">
      <span class="title-light">Trim Venture</span>
      <span class="growth-icon" role="img" aria-label="Illustration of a businessman beside rising bar chart with an upward arrow"></span>
      <span class="title-bold">Camp</span>
    </h1>
    <p class="tagline">Your Blueprint for Building a Profitable, Sustainable Business in Today's Economy!</p>
  </header>
</body>
</html>
```